Dietitian needs awesome business card

I need a contemporary design that's eye catching but professional.
My card is to given to doctors, specialists and patients alike.
I manage patients with chronic diseases
I have uploaded my logo and current business card, I would also like the other Certified Clinical Nutritionist logo incorporated into the design

Target Market(s)

Doctors, specialists and patients

Industry/Entity Type

Healthcare

Contact Information for Business Card

www.brightfieldnutrition.com.au
Ph: 0427 561 903
Fax: 6457 2183
email: marcus.k.diet@fernmail.com
Space on the back of the card with: Appointment date, Appointment time and appointment location

Font styles to use
Serif

Colors
fbee3e
876aae
ffc214

Requirements
Must have
• My Logo
• Certified Clinical Nutritionist Logo
• My 4 locations - Pinebrook Medical Centre, North Corrin Health, Hollis Medical, Ashcombe Doctors Surgery
Nice to have
• I like the colours in my current business card

```html
<!DOCTYPE html>
<html lang="en">
<head>
<meta charset="utf-8">
<title>Brightfield Nutrition &amp; Dietetics – Business Card</title>
<link href="https://fonts.googleapis.com/css2?family=Open+Sans:wght@400;600;700&family=Crimson+Text:ital@0;1&display=swap" rel="stylesheet">
<style>
  :root {
    --bg: #e9e6e1;
    --card: #ffffff;
    --blue-deep: #1f5fae;
    --blue: #0a8fc7;
    --teal: #28b3d6;
    --green: #8cc63f;
    --green-dark: #6fae2a;
    --ink-blue: #2a5aa8;
    --grey: #6b6f76;
    --line: #3b5f9c;
    --badge: #f0a63a;
  }
  * { margin: 0; padding: 0; box-sizing: border-box; }
  html, body { width: 1200px; height: 1023px; overflow: hidden; background: var(--bg); }
  .canvas { position: relative; width: 1200px; height: 1023px; }
  .card {
    position: absolute; left: 180px; width: 840px; height: 480px;
    background: var(--card); border-radius: 22px; overflow: hidden;
    box-shadow: 0 6px 18px rgba(0,0,0,.18);
  }
  .card-front { top: 20px; }
  .card-back { top: 523px; }
  .card svg.shapes { position: absolute; inset: 0; }

  /* front */
  .brand { position: absolute; left: 230px; top: 150px; display: flex; align-items: center; gap: 16px; }
  .brand-dot { width: 70px; height: 70px; border-radius: 50%; background: var(--blue); flex: none; }
  .brand-name { font-family: "Open Sans", sans-serif; font-weight: 400; color: var(--ink-blue); line-height: 1.05; white-space: nowrap; }
  .brand-name .main { display: block; font-size: 54px; }
  .brand-name .sub { display: block; font-size: 22px; }
  .person { position: absolute; left: 44px; top: 350px; font-family: "Open Sans", sans-serif; }
  .person-name { font-size: 30px; font-weight: 700; color: var(--ink-blue); }
  .person-title { font-size: 17px; color: var(--green-dark); margin-top: 2px; }
  .contacts { position: absolute; left: 360px; top: 318px; font-family: "Open Sans", sans-serif; font-size: 16px; color: var(--grey); list-style: none; white-space: nowrap; }
  .contacts li { display: flex; align-items: center; gap: 12px; height: 30px; }
  .contacts svg { width: 16px; height: 16px; flex: none; }
  .accreditation-badge { position: absolute; left: 716px; top: 398px; width: 54px; height: 54px; background: var(--badge); border-radius: 4px; }

  /* back */
  .appointment { position: absolute; left: 60px; top: 40px; width: 440px; font-family: "Crimson Text", serif; font-style: italic; color: var(--line); }
  .appointment h2 { font-weight: 400; font-size: 40px; color: var(--blue); text-align: center; margin: 0 0 12px; }
  .field { display: flex; align-items: flex-end; gap: 8px; font-size: 18px; height: 62px; border-bottom: 1px solid var(--line); padding-bottom: 4px; }
  .field.split { border-bottom: none; }
  .field.split span.part { flex: 1; display: flex; align-items: flex-end; border-bottom: 1px solid var(--line); padding-bottom: 4px; height: 100%; }
  .field.split span.part + span.part { margin-left: 20px; }
  .back-brand { position: absolute; left: 560px; top: 180px; display: flex; align-items: center; gap: 12px; }
  .back-brand .brand-dot { background: #ffffff; width: 54px; height: 54px; }
  .back-brand .brand-name { color: #ffffff; font-family: "Crimson Text", serif; }
  .back-brand .brand-name .main { font-size: 40px; }
  .back-brand .brand-name .sub { font-size: 18px; }
</style>
</head>
<body>
<main class="canvas">

  <section class="card card-front" aria-label="Business card front">
    <svg class="shapes" viewBox="0 0 840 480" width="840" height="480" aria-hidden="true">
      <defs>
        <linearGradient id="blueBand" x1="0" y1="0" x2="1" y2="1">
          <stop offset="0" stop-color="#3cc0e0"/>
          <stop offset="0.6" stop-color="#1a8fd0"/>
          <stop offset="1" stop-color="#1f4fae"/>
        </linearGradient>
        <linearGradient id="greenBand" x1="0" y1="0" x2="1" y2="1">
          <stop offset="0" stop-color="#b5d94a"/>
          <stop offset="1" stop-color="#6fae2a"/>
        </linearGradient>
      </defs>
      <path d="M320 0 Q700 20 840 330 L840 0 Z" fill="url(#blueBand)"/>
      <path d="M540 98 Q780 150 815 480 L840 480 L840 395 Q760 120 540 98 Z" fill="url(#greenBand)"/>
    </svg>

    <div class="brand">
      <span class="brand-dot"></span>
      <span class="brand-name"><span class="main">Brightfield</span><span class="sub">Nutrition &amp; Dietetics</span></span>
    </div>

    <div class="person">
      <div class="person-name">Marcus Kellaway</div>
      <div class="person-title">Certified Clinical Nutritionist</div>
    </div>

    <ul class="contacts">
      <li><svg viewBox="0 0 16 16"><circle cx="8" cy="8" r="7" fill="none" stroke="#8cc63f" stroke-width="1.5"/><path d="M5.5 4.5 L7 6 L6 7 Q7 9 9 10 L10 9 L11.5 10.5 L10.5 11.5 Q6 11 4.5 5.5 Z" fill="#8cc63f"/></svg>0427 561 903</li>
      <li><svg viewBox="0 0 16 16"><rect x="2" y="5" width="12" height="8" rx="1" fill="#8cc63f"/><rect x="4" y="2" width="8" height="4" fill="#8cc63f" opacity=".6"/></svg>6457 2183</li>
      <li><svg viewBox="0 0 16 16"><circle cx="8" cy="8" r="7" fill="none" stroke="#8cc63f" stroke-width="1.5"/><path d="M1 8 H15 M8 1 V15" stroke="#8cc63f" stroke-width="1.2"/></svg>www.brightfieldnutrition.com.au</li>
    </ul>
    <div class="accreditation-badge" role="img" aria-label="Accreditation badge"></div>
  </section>

  <section class="card card-back" aria-label="Business card back">
    <svg class="shapes" viewBox="0 0 840 480" width="840" height="480" aria-hidden="true">
      <defs>
        <linearGradient id="backBlue" x1="0" y1="0" x2="1" y2="1">
          <stop offset="0" stop-color="#10b0dc"/>
          <stop offset="1" stop-color="#0a6fb0"/>
        </linearGradient>
      </defs>
      <rect x="0" y="0" width="22" height="480" fill="#0a7fbf"/>
      <rect x="520" y="0" width="320" height="480" fill="url(#backBlue)"/>
    </svg>

    <div class="appointment">
      <h2>Appointment</h2>
      <div class="field">Name</div>
      <div class="field">Appointment date</div>
      <div class="field split"><span class="part">Appointment Location</span><span class="part">Time</span></div>
    </div>

    <div class="back-brand">
      <span class="brand-dot"></span>
      <span class="brand-name"><span class="main">Brightfield</span><span class="sub">Nutrition &amp; Dietetics</span></span>
    </div>
  </section>

</main>
</body>
</html>
```